business card

Business card for new business.
Red and black corporate colors.
Card can have an Indsutrial feel to it. Feel free to add Rust, Bolted steel, or graphics as you see fit. We provide highly specialized services to the below mentioned industries.
Keep information out of corners so that if I want I can choose rounded corners.
Information
- front. name - title - phone - email
- Rear
Refining - Rail - Infrastructure - Mining - Energy
Calgary - Edmonton - Fort McMurray - Revelstoke - Vancouver

```html
<!DOCTYPE html>
<html lang="en">
<head>
<meta charset="utf-8">
<title>Girderline Business Card</title>
<link href="https://fonts.googleapis.com/css2?family=Roboto:wght@400;500&family=Roboto+Condensed:wght@700&display=swap" rel="stylesheet">
<style>
  :root {
    --backdrop: #e4e2df;
    --card-front: #f6f6f6;
    --card-back: #1a1a1c;
    --brand-red: #e30613;
    --wordmark-grey: #6e6e6e;
    --text-grey: #555555;
    --text-light: #ffffff;
  }
  * { margin: 0; padding: 0; box-sizing: border-box; }
  html, body {
    width: 1200px; height: 960px; overflow: hidden;
    background: var(--backdrop);
    font-family: "Roboto", Arial, sans-serif;
  }
  .stage { position: relative; width: 1200px; height: 960px; }
  .card {
    position: absolute; width: 600px; height: 343px;
    box-shadow: 0 2px 6px rgba(0,0,0,.25);
  }
  .card--front { left: 314px; top: 113px; background: var(--card-front); }
  .card--back { left: 311px; top: 472px; height: 342px; background: var(--card-back); }

  .wordmark {
    position: absolute; left: 36px; top: 52px;
    font-family: "Roboto Condensed", "Arial Narrow", sans-serif;
    font-weight: 700; font-size: 46px; line-height: 1;
    color: var(--wordmark-grey); letter-spacing: 0.5px;
  }

  .contact { position: absolute; left: 40px; top: 241px; list-style: none; }
  .contact li {
    display: flex; align-items: center; height: 19px;
    font-size: 14.5px; color: var(--text-grey);
  }
  .contact svg { width: 13px; height: 13px; margin-right: 9px; fill: var(--brand-red); flex: none; }

  .name-tab { position: absolute; left: 394px; top: 232px; width: 206px; height: 69px; }
  .name-tab svg { position: absolute; inset: 0; }
  .name-tab__text { position: absolute; right: 30px; top: 10px; text-align: right; color: var(--text-light); }
  .name-tab__name {
    font-family: "Roboto Condensed", "Arial Narrow", sans-serif;
    font-weight: 700; font-size: 23px; line-height: 1.1;
  }
  .name-tab__title { font-size: 15px; font-weight: 500; line-height: 1.3; }

  .brand-square {
    position: absolute; left: 169px; top: 124px;
    width: 108px; height: 108px; background: var(--brand-red);
  }
  .sector-list { position: absolute; left: 300px; top: 76px; list-style: none; }
  .sector-list li {
    position: relative; padding-left: 12px;
    font-size: 14.5px; line-height: 19px; color: var(--text-light);
  }
  .sector-list li::before {
    content: ""; position: absolute; left: 1px; top: 7px;
    width: 4px; height: 4px; border-radius: 50%; background: var(--brand-red);
  }
</style>
</head>
<body>
<main class="stage">
  <section class="card card--front" aria-label="Card front">
    <div class="wordmark">GIRDERLINE</div>

    <ul class="contact">
      <li>
        <svg viewBox="0 0 24 24" aria-hidden="true"><path d="M6.6 10.8a15.1 15.1 0 0 0 6.6 6.6l2.2-2.2c.3-.3.7-.4 1-.2 1.1.4 2.3.6 3.6.6.6 0 1 .4 1 1V20c0 .6-.4 1-1 1C10.6 21 3 13.4 3 4c0-.6.4-1 1-1h3.5c.6 0 1 .4 1 1 0 1.3.2 2.5.6 3.6.1.3 0 .7-.2 1z"/></svg>
        555 014 2290
      </li>
      <li>
        <svg viewBox="0 0 24 24" aria-hidden="true"><path d="M2 5h20v14H2z M2 5l10 8 10-8" /><path d="M2 6.5l10 7.5 10-7.5V19H2z" fill="#fff" opacity=".35"/></svg>
        info@girderline.com
      </li>
      <li>
        <svg viewBox="0 0 24 24" aria-hidden="true"><circle cx="12" cy="12" r="10"/><path d="M7 7c2 1 3 0 4 2s-2 3 0 5 3 3 2 6M15 4c0 2 2 2 3 4s3 3 2 5" stroke="#fff" stroke-width="1.6" fill="none"/></svg>
        www.girderline.com
      </li>
    </ul>

    <div class="name-tab">
      <svg viewBox="0 0 206 69" width="206" height="69" aria-hidden="true">
        <path d="M22 0H206V69H22Q14 69 10 60L2 40Q0 34.5 2 29L10 9Q14 0 22 0Z" fill="var(--brand-red)"/>
      </svg>
      <div class="name-tab__text">
        <div class="name-tab__name">DANIEL REYES</div>
        <div class="name-tab__title">CEO/FOUNDER</div>
      </div>
    </div>
  </section>

  <section class="card card--back" aria-label="Card back">
    <div class="brand-square" aria-hidden="true"></div>
    <ul class="sector-list">
      <li>Refining</li>
      <li>Rail</li>
      <li>Infrastructure</li>
      <li>Mining</li>
      <li>Energy</li>
      <li>Calgary</li>
      <li>Edmonton</li>
      <li>Fort McMurray</li>
      <li>Revelstoke</li>
      <li>Vancouver</li>
    </ul>
  </section>
</main>
</body>
</html>
```